Mara Penrith Copywriter Website

I am starting a new business as a freelance copywriter. Trying to set up the website for my business is proving to be too technical for me. I would like a simple, clean website using primarily black and white. I have attached the logo I would like used. I would like the menu icons to be Home, Services, Portfolio, Blog, Contact. I would like my mobile phone number (0412 583 906) and email address (mara.penrith.copywriter@fernmail.test) used in the header of the site. I need the site to be easily manageable and inter-changeable for me to be able to move things around and add images, etc with ease.

I would like the home page to be a static page with space for an image of myself somewhere (I haven't had this taken as yet), an area to put a bit about myself and my business, and also somewhere to include social media icons/links. Again, I would like the whole website and home page to be easily managed so that I can add/delete things with ease.

I would like the image of the typewriter used in the website somewhere also please.

Coding

Coded - Design and coding required

Number of Pages Required

5+ page

Font styles to use
Sans Serif
Script

Colors
fdf0f6

Requirements
Must have
• The logo provided
• Ability to change page contents easily
• Ability to add social media icons as needed
Nice to have
• Use of the typewriter image
Should not have
• Complicated pages that are not easily editable

```html
<!DOCTYPE html>
<html lang="en">
<head>
<meta charset="utf-8">
<title>Mara Penrith Copywriter</title>
<link href="https://fonts.googleapis.com/css2?family=Montserrat:wght@400;600;700&family=Raleway:wght@300;400;600;700&family=Open+Sans:wght@400;600&display=swap" rel="stylesheet">
<style>
:root{
  --black:#111111;
  --ink:#1c1c1c;
  --dark:#2a2a2a;
  --grey:#8a8a8a;
  --light:#dddddd;
  --white:#ffffff;
  --blush:#fdf0f6;
  --blush-deep:#f3dbe5;
}
*{box-sizing:border-box;margin:0;padding:0}
html,body{width:1200px;height:3056px;overflow:hidden}
body{font-family:"Open Sans",Arial,sans-serif;color:var(--ink);background:var(--white);position:relative}
/* header */
.site-header{height:60px;display:flex;align-items:center;padding:0 60px 0 128px;background:var(--white)}
.brand{display:flex;align-items:center;gap:10px;background:var(--blush-deep);padding:8px 16px;width:208px}
.brand-name{font-family:"Raleway",sans-serif;font-weight:600;font-size:15px;color:var(--ink)}
.brand-dot{width:12px;height:12px;border-radius:50%;background:var(--ink)}
.main-nav{display:flex;gap:22px;margin-left:132px;font-family:"Montserrat",sans-serif;font-size:12px;font-weight:600}
.main-nav a{color:var(--ink);text-decoration:none}
.main-nav a.active{border-bottom:2px solid var(--ink);padding-bottom:3px}
.header-contact{margin-left:auto;font-size:12px;line-height:22px}
.header-contact div{display:flex;align-items:center;gap:8px}
/* hero */
.hero{position:relative;height:580px;background:linear-gradient(120deg,#3d3d3d 0%,#1f1f1f 45%,#4a4a4a 75%,#2b2b2b 100%);color:var(--white);text-align:center}
.hero-title{padding-top:232px;font-family:"Montserrat",sans-serif;font-weight:700;font-size:50px;letter-spacing:2px}
.hero-sub{font-family:"Raleway",sans-serif;font-size:32px;margin-top:4px}
.btn{display:inline-block;background:var(--black);color:var(--white);font-family:"Montserrat",sans-serif;font-weight:600;font-size:15px;padding:16px 28px;text-decoration:none}
.hero .btn{margin-top:30px}
.slide-arrow{position:absolute;top:370px;width:44px;height:44px;border-radius:50%;background:rgba(0,0,0,.55);display:flex;align-items:center;justify-content:center}
.slide-arrow.left{left:12px}.slide-arrow.right{right:12px}
/* about */
.about{height:700px;position:relative}
.about-photo{position:absolute;left:80px;top:140px;width:320px;height:400px;background:radial-gradient(circle at 50% 55%,#3a3a3a 0%,#6b6b6b 45%,#f4f4f4 75%)}
.about-text{position:absolute;left:480px;top:138px;width:640px}
.eyebrow{font-family:"Montserrat",sans-serif;font-weight:700;font-size:22px}
.about-title{font-family:"Raleway",sans-serif;font-size:38px;font-weight:400;letter-spacing:1px;margin:4px 0 22px}
.about-text p{font-size:13.5px;line-height:24px;color:#555;margin-bottom:14px;width:600px}
.about .btn{margin-top:20px}
/* services */
.services{height:440px;background:linear-gradient(180deg,#262626,#1a1a1a);color:var(--white);text-align:center;padding-top:56px}
.services .eyebrow{font-size:20px}
.section-title{font-family:"Raleway",sans-serif;font-weight:400;font-size:38px;letter-spacing:1px}
.service-grid{display:grid;grid-template-columns:repeat(3,350px);row-gap:46px;margin:44px 0 0 80px;text-align:left}
.service{display:flex;gap:20px;align-items:flex-start}
.service-icon{width:84px;height:84px;border-radius:50%;background:var(--blush);flex:none;display:flex;align-items:center;justify-content:center}
.service h3{font-family:"Montserrat",sans-serif;font-size:18px;font-weight:600;margin:4px 0 6px}
.service p{font-size:12px;line-height:19px;color:#9a9a9a;width:190px}
/* cta */
.cta{height:400px;background:var(--blush);text-align:center;padding-top:140px}
.cta h2{font-family:"Montserrat",sans-serif;font-weight:700;font-size:34px;line-height:44px;color:var(--ink)}
.cta-line{display:flex;justify-content:center;align-items:center;gap:24px;margin-top:28px;font-family:"Montserrat",sans-serif;font-weight:700;font-size:40px;color:var(--white);-webkit-text-stroke:1px #bbb}
.cta-phone{width:80px;height:80px;border-radius:50%;background:var(--black);display:flex;align-items:center;justify-content:center;-webkit-text-stroke:0}
/* portfolio */
.portfolio{height:530px;position:relative;padding:50px 0 0 80px}
.portfolio .eyebrow{font-size:20px}
.work{position:absolute;top:160px;width:420px;height:320px}
.work.one{left:140px;background:linear-gradient(135deg,#e6e6e6,#8c8c8c 55%,#4a4a4a)}
.work.two{left:620px;background:linear-gradient(135deg,#d0d0d0,#5a5a5a 50%,#202020)}
.zoom{position:absolute;right:0;bottom:0;width:56px;height:56px;background:var(--white);display:flex;align-items:center;justify-content:center}
.carousel-arrow{position:absolute;top:280px;font-size:60px;font-weight:300;font-family:"Raleway",sans-serif;color:var(--ink)}
/* footer */
.site-footer{height:290px;background:var(--dark);color:var(--white);display:flex;padding:28px 0 0 80px}
.footer-col h4{font-family:"Montserrat",sans-serif;font-size:16px;font-weight:600;margin-bottom:16px}
.footer-about{width:320px}
.footer-brand{background:var(--blush-deep);width:200px;padding:8px 14px;margin-bottom:20px}
.footer-about p{font-size:12px;line-height:20px;color:#bbb}
.read-more{font-size:13px;font-weight:600;margin-top:10px;display:block}
.footer-contact{width:360px;margin-left:40px;font-size:12px;color:#ccc}
.footer-contact li{list-style:none;display:flex;gap:10px;margin-bottom:12px;line-height:18px}
.social{display:flex;gap:12px;margin-top:10px}
.social-link{width:40px;height:40px;border-radius:50%;background:var(--white);display:flex;align-items:center;justify-content:center}
.footer-news{width:300px;margin-left:20px}
.footer-news p{font-size:12px;color:#ccc;margin-bottom:12px}
.field{width:260px;height:32px;background:#3a3a3a;border:1px solid #555;font-size:12px;color:#999;padding:7px 10px;margin-bottom:10px}
.subscribe{display:inline-block;border:2px solid var(--white);border-radius:20px;padding:8px 22px;font-family:"Montserrat",sans-serif;font-size:13px;font-weight:600;margin-top:4px}
.copyright{height:56px;background:var(--black);color:#ccc;font-size:13px;text-align:center;line-height:56px}
</style>
</head>
<body>
<header class="site-header">
  <div class="brand"><span class="brand-dot"></span><span class="brand-name">Mara Penrith</span></div>
  <nav class="main-nav"><a class="active" href="#">HOME</a><a href="#">SERVICES</a><a href="#">PORTFOLIO</a><a href="#">BLOG</a><a href="#">CONTACT</a></nav>
  <div class="header-contact">
    <div><svg width="12" height="12" viewBox="0 0 24 24"><path d="M6 2l4 4-2 3c1 3 4 6 7 7l3-2 4 4-3 4C10 22 2 14 2 5z" fill="#111"/></svg>0412 583 906</div>
    <div><svg width="12" height="10" viewBox="0 0 24 18"><rect x="1" y="1" width="22" height="16" fill="none" stroke="#111" stroke-width="2"/><path d="M1 1l11 9 11-9" fill="none" stroke="#111" stroke-width="2"/></svg>mara.penrith.copywriter@fernmail.test</div>
  </div>
</header>

<section class="hero" role="img" aria-label="Dimmed photo of a writer working at a laptop on a desk">
  <h1 class="hero-title">MARA PENRITH</h1>
  <p class="hero-sub">Ready To Freelance As A Copywriter?</p>
  <a class="btn" href="#">GET STARTED</a>
  <span class="slide-arrow left"><svg width="14" height="14" viewBox="0 0 14 14"><path d="M9 2L4 7l5 5" stroke="#fff" stroke-width="2" fill="none"/></svg></span>
  <span class="slide-arrow right"><svg width="14" height="14" viewBox="0 0 14 14"><path d="M5 2l5 5-5 5" stroke="#fff" stroke-width="2" fill="none"/></svg></span>
</section>

<section class="about">
  <div class="about-photo" role="img" aria-label="Vintage black typewriter with a sheet of paper"></div>
  <div class="about-text">
    <p class="eyebrow">WELCOME TO</p>
    <h2 class="about-title">MARA PENRITH COPYWRITER</h2>
    <p>Lorem Ipsum is simply dummy text of the printing and typesetting industry. Lorem Ipsum has been the industry's standard dummy text ever since the 1500s, when an unknown printer took a galley of type and scrambled.</p>
    <p>Lorem Ipsum is simply dummy text of the printing and typesetting industry. Lorem Ipsum has been the industry's standard dummy text ever since the 1500s, when an unknown printer took a galley of type and scrambled.</p>
    <a class="btn" href="#">LEARN MORE</a>
  </div>
</section>

<section class="services">
  <p class="eyebrow">WHAT WE DO</p>
  <h2 class="section-title">OUR SERVICES</h2>
  <div class="service-grid">
    <div class="service"><span class="service-icon"><svg width="40" height="40" viewBox="0 0 40 40"><rect x="4" y="6" width="32" height="28" fill="none" stroke="#111" stroke-width="3"/><path d="M4 13h32M10 19h10M10 25h20" stroke="#111" stroke-width="3"/></svg></span><div><h3>APP</h3><p>Lorem ipsum is simply the text of the printing &amp; type setting industry has.</p></div></div>
    <div class="service"><span class="service-icon"><svg width="40" height="40" viewBox="0 0 40 40"><rect x="12" y="6" width="16" height="16" fill="#111"/><rect x="4" y="22" width="32" height="5" fill="#111"/><circle cx="14" cy="32" r="4" fill="none" stroke="#111" stroke-width="2"/><circle cx="26" cy="32" r="4" fill="none" stroke="#111" stroke-width="2"/></svg></span><div><h3>BRAND</h3><p>Lorem ipsum is simply the text of the printing &amp; type setting industry has.</p></div></div>
    <div class="service"><span class="service-icon"><svg width="40" height="40" viewBox="0 0 40 40"><circle cx="20" cy="20" r="14" fill="none" stroke="#111" stroke-width="3"/><path d="M6 20h28M20 6c-8 8-8 20 0 28M20 6c8 8 8 20 0 28" fill="none" stroke="#111" stroke-width="2"/></svg></span><div><h3>SOCIAL</h3><p>Lorem ipsum is simply the text of the printing &amp; type setting industry has.</p></div></div>
    <div class="service"><span class="service-icon"><svg width="40" height="40" viewBox="0 0 40 40"><path d="M20 5a10 10 0 0 0-6 18v5h12v-5a10 10 0 0 0-6-18z" fill="#111"/><rect x="15" y="30" width="10" height="4" fill="#111"/></svg></span><div><h3>IDEATION</h3><p>Lorem ipsum is simply the text of the printing &amp; type setting industry has.</p></div></div>
    <div class="service"><span class="service-icon"><svg width="40" height="40" viewBox="0 0 40 40"><rect x="8" y="4" width="24" height="32" fill="none" stroke="#111" stroke-width="3"/><path d="M8 11h24M8 29h24M14 4v32M26 4v32" stroke="#111" stroke-width="2"/></svg></span><div><h3>VFX</h3><p>Lorem ipsum is simply the text of the printing &amp; type setting industry has.</p></div></div>
    <div class="service"><span class="service-icon"><svg width="40" height="40" viewBox="0 0 40 40"><rect x="4" y="8" width="32" height="24" fill="none" stroke="#111" stroke-width="3"/><path d="M16 14l10 6-10 6z" fill="#111"/></svg></span><div><h3>FILMS</h3><p>Lorem ipsum is simply the text of the printing &amp; type setting industry has.</p></div></div>
  </div>
</section>

<section class="cta">
  <h2>IF YOU NEED AN HAVE QUESTION PLEASE<br>CONTACT US TODAY</h2>
  <div class="cta-line"><span>CALL US ON</span><span class="cta-phone"><svg width="34" height="34" viewBox="0 0 24 24"><path d="M6 2l4 4-2 3c1 3 4 6 7 7l3-2 4 4-3 4C10 22 2 14 2 5z" fill="#fff"/></svg></span><span>555-014-2298</span></div>
</section>

<section class="portfolio">
  <p class="eyebrow">OUR WORKS</p>
  <h2 class="section-title">OUR PORTFOLIO</h2>
  <span class="carousel-arrow" style="left:72px">‹</span>
  <div class="work one" role="img" aria-label="Hands typing on a laptop keyboard"><span class="zoom"><svg width="24" height="24" viewBox="0 0 24 24"><circle cx="10" cy="10" r="7" fill="none" stroke="#111" stroke-width="2.5"/><path d="M15 15l7 7" stroke="#111" stroke-width="3"/></svg></span></div>
  <div class="work two" role="img" aria-label="Laptop on a desk being used"><span class="zoom"><svg width="24" height="24" viewBox="0 0 24 24"><circle cx="10" cy="10" r="7" fill="none" stroke="#111" stroke-width="2.5"/><path d="M15 15l7 7" stroke="#111" stroke-width="3"/></svg></span></div>
  <span class="carousel-arrow" style="left:1098px">›</span>
</section>

<footer class="site-footer">
  <div class="footer-col footer-about">
    <div class="footer-brand"><span class="brand-name">Mara Penrith</span></div>
    <p>Lorem Ipsum is simply dummy text of the printing and typesetting industry. Lorem Ipsum has been the industry's standard.</p>
    <span class="read-more">Read More... »</span>
  </div>
  <div class="footer-col footer-contact">
    <h4>CONTACT US</h4>
    <ul>
      <li><svg width="12" height="16" viewBox="0 0 12 16"><path d="M6 0a6 6 0 0 0-6 6c0 4 6 10 6 10s6-6 6-10a6 6 0 0 0-6-6z" fill="#fff"/></svg>N/8, Lorem ipsum dolor sit,<br>Sed ut perspiciatis unde</li>
      <li><svg width="12" height="12" viewBox="0 0 24 24"><path d="M6 2l4 4-2 3c1 3 4 6 7 7l3-2 4 4-3 4C10 22 2 14 2 5z" fill="#fff"/></svg>0412 583 906</li>
      <li><svg width="12" height="10" viewBox="0 0 24 18"><rect x="1" y="1" width="22" height="16" fill="none" stroke="#fff" stroke-width="2"/><path d="M1 1l11 9 11-9" fill="none" stroke="#fff" stroke-width="2"/></svg>mara.penrith.copywriter@fernmail.test</li>
    </ul>
    <div class="social">
      <a class="social-link" href="#" aria-label="Social link"><svg width="18" height="18" viewBox="0 0 24 24"><path d="M10 14a5 5 0 0 0 7 0l3-3a5 5 0 0 0-7-7l-1 1M14 10a5 5 0 0 0-7 0l-3 3a5 5 0 0 0 7 7l1-1" fill="none" stroke="#111" stroke-width="2.5" stroke-linecap="round"/></svg></a>
      <a class="social-link" href="#" aria-label="Share"><svg width="18" height="18" viewBox="0 0 24 24"><circle cx="18" cy="5" r="3" fill="#111"/><circle cx="6" cy="12" r="3" fill="#111"/><circle cx="18" cy="19" r="3" fill="#111"/><path d="M8 11l8-5M8 13l8 5" stroke="#111" stroke-width="2"/></svg></a>
      <a class="social-link" href="#" aria-label="Website"><svg width="18" height="18" viewBox="0 0 24 24"><circle cx="12" cy="12" r="9" fill="none" stroke="#111" stroke-width="2"/><path d="M3 12h18M12 3c-5 5-5 13 0 18M12 3c5 5 5 13 0 18" fill="none" stroke="#111" stroke-width="1.6"/></svg></a>
    </div>
  </div>
  <div class="footer-col footer-news">
    <h4>NEWSLETTER</h4>
    <p>Sign up for Blog and updates !</p>
    <div class="field">Enter Email</div>
    <div class="field">Enter Email</div>
    <span class="subscribe">SUBSCRIBE</span>
  </div>
</footer>
<div class="copyright">©mara penrith copywriter - 2016 All Right Reserved.</div>
</body>
</html>
```